Retail Jewelry Business Card Design Project

We are in need of a new business card design for a retail jewelry store. This store is in the business of fine jewelry including but not specific to bridal jewelry, diamonds, designer jewelry and watches.

This store has been in business for 20 years but continues to strive for a modern professional appeal. The main colors use for this business are a royal blue, white and silver.

Target Market(s)

Target market is ages 18-50

Industry/Entity Type

Jewelry

Requirements
Must have
• Sales Person Name
Sales Person Email Address

Store Address
Store Phone
Website

Standard business card size. No odd shapes or sizes.
Nice to have
• Overall modern feel for card.

We have thought that a design with a nice feature of the logo on the back of the card would be nice but open to ideas.
Should not have
• No specific images of jewelry should be used.

```html
<!DOCTYPE html>
<html lang="en">
<head>
<meta charset="utf-8">
<title>Mason Reed Fine Jewelry — Business Card</title>
<link rel="stylesheet" href="https://fonts.googleapis.com/css2?family=Cinzel:wght@600&family=Roboto:wght@400;700&display=swap">
<style>
  :root {
    --royal: #2b2a9e;
    --royal-deep: #1c1a72;
    --royal-light: #3836b8;
    --silver: #d9dbe4;
    --white: #ffffff;
    --paper: #f4f4f7;
    --backdrop: #e6e6ea;
    --ink-soft: #e8e8f6;
  }
  * { box-sizing: border-box; margin: 0; padding: 0; }
  html, body {
    width: 1200px;
    height: 1000px;
    overflow: hidden;
  }
  body {
    background: var(--backdrop);
    font-family: "Roboto", Arial, sans-serif;
    position: relative;
  }
  .card {
    position: absolute;
    left: 280px;
    width: 640px;
    height: 366px;
    border-radius: 4px;
    overflow: hidden;
    box-shadow: 0 6px 18px rgba(0,0,0,0.18);
  }
  .brand {
    display: flex;
    align-items: center;
    justify-content: center;
    gap: 12px;
    white-space: nowrap;
  }
  .brand-dot {
    flex: 0 0 auto;
    border-radius: 50%;
  }
  .brand-name {
    font-family: "Cinzel", Georgia, serif;
    font-weight: 600;
    letter-spacing: 1px;
  }

  /* Back: contact side */
  .card--back {
    top: 90px;
    background: var(--white);
    display: flex;
    flex-direction: column;
  }
  .back__brand {
    flex: 0 0 140px;
    padding: 0 72px;
    background: linear-gradient(180deg, var(--white), var(--paper));
  }
  .back__brand .brand-dot {
    width: 10px;
    height: 10px;
    background: var(--royal);
  }
  .back__brand .brand-name {
    font-size: 25px;
    color: var(--royal);
  }
  .back__band {
    flex: 0 0 112px;
    background: var(--royal);
    color: var(--ink-soft);
    display: flex;
    flex-direction: column;
    align-items: center;
    justify-content: center;
    gap: 12px;
  }
  .person-name { font-size: 20px; }
  .person-contact { font-size: 16px; letter-spacing: 0.3px; }
  .back__store {
    flex: 1;
    display: flex;
    flex-direction: column;
    align-items: center;
    justify-content: center;
    gap: 10px;
    color: var(--royal);
  }
  .store-address { font-size: 16px; }
  .store-web {
    font-size: 20px;
    font-weight: 700;
    letter-spacing: 1.5px;
  }

  /* Front: logo side */
  .card--front {
    top: 520px;
    padding: 0 64px;
    background: radial-gradient(ellipse at 50% 45%, var(--royal-light) 0%, var(--royal) 55%, var(--royal-deep) 100%);
    gap: 14px;
  }
  .card--front .brand-dot {
    width: 12px;
    height: 12px;
    background: var(--silver);
  }
  .card--front .brand-name {
    font-size: 30px;
    color: var(--silver);
  }
</style>
</head>
<body>
  <section class="card card--back" aria-label="Business card, contact side">
    <div class="brand back__brand">
      <span class="brand-dot"></span>
      <span class="brand-name">Mason Reed Fine Jewelry</span>
    </div>
    <div class="back__band">
      <p class="person-name">Mason Reed Callahan</p>
      <p class="person-contact">0400 555 123 | mason@masonreedjewelry.com</p>
    </div>
    <div class="back__store">
      <p class="store-address">1520 Harbor Avenue, Bayview, FL 32000</p>
      <p class="store-web">MASONREEDJEWELRY.COM</p>
    </div>
  </section>

  <section class="card card--front brand" aria-label="Business card, logo side">
    <span class="brand-dot"></span>
    <span class="brand-name">Mason Reed Fine Jewelry</span>
  </section>
</body>
</html>
```